Need Flyer for Our Real estate Agency

Need to run General Campaign for our agency with Start of New Year as our theme ..Must have an agent's picture on the DL..
Address:
27 / 486Brindle rd, Marsden VIC 3047
Ph:03 9412 7306
email:info@kovalinrealestate.com.au
www.kovalinrealestate.com.au
Something like as attached picture..
Target Market(s)
Home Buyers
Industry/Entity Type
Real Estate Agent
Requirements
Must have
- Our Logo Colours

```html
<!DOCTYPE html>
<html lang="en">
<head>
<meta charset="utf-8">
<title>Kovalin Real Estate – New Year DL Flyer</title>
<link rel="stylesheet" href="https://fonts.googleapis.com/css2?family=Lato:wght@300;400;700&display=swap">
<style>
  :root {
    --navy: #0f2a66;
    --navy-deep: #0a1f4d;
    --navy-light: #1b3a80;
    --maroon: #7c1620;
    --white: #ffffff;
    --grey-arc: #c9ccd2;
    --page: #ececec;
  }
  * { margin: 0; padding: 0; box-sizing: border-box; }
  html, body { width: 1200px; height: 1199px; overflow: hidden; }
  body {
    background: var(--page);
    font-family: "Lato", Arial, sans-serif;
    color: var(--white);
    position: relative;
  }
  .flyer {
    position: absolute;
    left: 117px;
    width: 966px;
    height: 460px;
    overflow: hidden;
    box-shadow: 0 4px 12px rgba(0,0,0,.25);
  }
  .flyer--front { top: 113px; }
  .flyer--back { top: 644px; }
  .flyer__art { position: absolute; inset: 0; width: 966px; height: 460px; display: block; }
  .brand-name {
    position: absolute;
    left: 480px; width: 440px;
    top: 128px;
    text-align: center;
    font-weight: 400;
    font-size: 30px;
    letter-spacing: 3px;
    white-space: nowrap;
    text-transform: uppercase;
  }
  .flyer--back .brand-name { top: 128px; }
  .headline {
    position: absolute;
    left: 490px; width: 420px;
    top: 196px;
    text-align: center;
    font-weight: 300;
    font-size: 31px;
    line-height: 45px;
  }
  .subline {
    position: absolute;
    left: 450px; width: 500px;
    top: 323px;
    text-align: center;
    font-size: 14.5px;
    white-space: nowrap;
    text-transform: uppercase;
  }
  .subline strong { font-weight: 700; }
  .call-button {
    position: absolute;
    left: 520px; width: 362px;
    top: 372px; height: 46px;
    background: var(--white);
    border-radius: 23px;
    color: var(--maroon);
    font-weight: 700;
    font-size: 19px;
    display: flex; align-items: center; justify-content: center; gap: 8px;
    box-shadow: 0 3px 6px rgba(0,0,0,.35);
  }
  .call-button svg { width: 20px; height: 20px; }
  .band-note {
    position: absolute;
    left: 450px; width: 500px;
    top: 426px;
    text-align: center;
    font-size: 17px;
    font-weight: 300;
  }
  .contact-list {
    position: absolute;
    left: 577px;
    top: 224px;
    list-style: none;
  }
  .contact-list li {
    display: flex; align-items: center; gap: 16px;
    height: 41px;
    font-size: 18px;
    font-weight: 300;
    white-space: nowrap;
  }
  .contact-list svg { width: 18px; height: 18px; }
  .address {
    position: absolute;
    left: 440px; width: 520px;
    top: 416px;
    text-align: center;
    font-size: 17px;
    font-weight: 300;
    white-space: nowrap;
  }
</style>
</head>
<body>

<section class="flyer flyer--front">
  <svg class="flyer__art" viewBox="0 0 966 460">
    <defs>
      <linearGradient id="navyFront" x1="0" y1="0" x2="1" y2="1">
        <stop offset="0" stop-color="#0a1f4d"/>
        <stop offset=".55" stop-color="#14337a"/>
        <stop offset="1" stop-color="#0d2760"/>
      </linearGradient>
      <linearGradient id="agentPhoto" x1="0" y1="0" x2="0" y2="1">
        <stop offset="0" stop-color="#9fb2cc"/>
        <stop offset=".55" stop-color="#8a8c8e"/>
        <stop offset="1" stop-color="#3e5a3a"/>
      </linearGradient>
    </defs>
    <rect class="panel-navy" width="966" height="460" fill="url(#navyFront)"/>
    <rect class="band-maroon" x="0" y="393" width="966" height="67" fill="var(--maroon)"/>
    <rect class="band-rule" x="0" y="386" width="966" height="3" fill="var(--white)"/>
    <path class="arc-grey" d="M0 0 H455 C515 150 505 330 425 460 H0 Z" fill="var(--grey-arc)"/>
    <path class="arc-white" d="M0 0 H425 C488 150 478 330 398 460 H0 Z" fill="var(--white)"/>
    <path class="agent-photo" role="img" aria-label="Smiling agent in a blue suit standing in front of a large two-storey family home at dusk" d="M0 0 H400 C462 150 452 330 375 460 H0 Z" fill="url(#agentPhoto)"/>
  </svg>
  <div class="brand-name">Kovalin Real Estate</div>
  <p class="headline">Curios to know what your<br>home is worth?</p>
  <p class="subline">Start of new year with <strong>Arjun Malhotra</strong> and find out!</p>
  <div class="call-button">
    <span>CALL ME NOW!</span>
    <svg viewBox="0 0 24 24"><circle cx="12" cy="12" r="10.5" fill="none" stroke="var(--maroon)" stroke-width="2"/><path d="M8.5 7c.6-.5 1.3-.4 1.6.2l.9 1.6c.3.5.1 1-.3 1.3l-.6.5c.5 1.3 1.6 2.5 2.9 3l.5-.6c.4-.4.9-.5 1.3-.2l1.6.9c.6.3.7 1 .2 1.6-1 1.1-2.3 1.4-3.7.7-2.2-1.1-4-2.9-5-5.1-.6-1.3-.4-2.8.6-3.9z" fill="var(--maroon)"/></svg>
    <span>03 9412 7306</span>
  </div>
  <p class="band-note">For Free property Appraisal</p>
</section>

<section class="flyer flyer--back">
  <svg class="flyer__art" viewBox="0 0 966 460">
    <defs>
      <linearGradient id="navyBack" x1="0" y1="0" x2="1" y2="1">
        <stop offset="0" stop-color="#0a1f4d"/>
        <stop offset=".55" stop-color="#14337a"/>
        <stop offset="1" stop-color="#0d2760"/>
      </linearGradient>
      <linearGradient id="housePhoto" x1="0" y1="0" x2="1" y2="1">
        <stop offset="0" stop-color="#1f3d4a"/>
        <stop offset=".5" stop-color="#b8705a"/>
        <stop offset="1" stop-color="#16303b"/>
      </linearGradient>
    </defs>
    <rect class="panel-navy" width="966" height="460" fill="url(#navyBack)"/>
    <rect class="band-maroon" x="0" y="393" width="966" height="67" fill="var(--maroon)"/>
    <rect class="band-rule" x="0" y="386" width="966" height="3" fill="var(--white)"/>
    <path class="arc-grey" d="M0 0 H455 C515 150 505 330 425 460 H0 Z" fill="var(--grey-arc)"/>
    <path class="arc-white" d="M0 0 H425 C488 150 478 330 398 460 H0 Z" fill="var(--white)"/>
    <path class="house-photo" role="img" aria-label="Two hands sheltering a small red model house held in front of a suited person" d="M0 0 H400 C462 150 452 330 375 460 H0 Z" fill="url(#housePhoto)"/>
  </svg>
  <div class="brand-name">Kovalin Real Estate</div>
  <ul class="contact-list">
    <li>
      <svg viewBox="0 0 24 24"><circle cx="12" cy="12" r="10.5" fill="none" stroke="var(--white)" stroke-width="2"/><path d="M8.5 7c.6-.5 1.3-.4 1.6.2l.9 1.6c.3.5.1 1-.3 1.3l-.6.5c.5 1.3 1.6 2.5 2.9 3l.5-.6c.4-.4.9-.5 1.3-.2l1.6.9c.6.3.7 1 .2 1.6-1 1.1-2.3 1.4-3.7.7-2.2-1.1-4-2.9-5-5.1-.6-1.3-.4-2.8.6-3.9z" fill="var(--white)"/></svg>
      <span>03 9412 7306</span>
    </li>
    <li>
      <svg viewBox="0 0 24 24"><circle cx="12" cy="12" r="10.5" fill="none" stroke="var(--white)" stroke-width="2"/><rect x="6.5" y="8" width="11" height="8" fill="none" stroke="var(--white)" stroke-width="1.5"/><path d="M6.5 8.5 12 12.5 17.5 8.5" fill="none" stroke="var(--white)" stroke-width="1.5"/></svg>
      <span>info@kovalinrealestate.com.au</span>
    </li>
    <li>
      <svg viewBox="0 0 24 24"><circle cx="12" cy="12" r="10.5" fill="none" stroke="var(--white)" stroke-width="2"/><circle cx="12" cy="12" r="6" fill="none" stroke="var(--white)" stroke-width="1.3"/><ellipse cx="12" cy="12" rx="2.6" ry="6" fill="none" stroke="var(--white)" stroke-width="1.3"/><path d="M6 12h12" stroke="var(--white)" stroke-width="1.3"/></svg>
      <span>www.kovalinrealestate.com.au</span>
    </li>
  </ul>
  <p class="address">27/486 Brindle Rd Marsden, Victoria, Australia 3047</p>
</section>

</body>
</html>
```